Tiskoro

We need a business card for our company is a holding for different business all are different we try to have some air of relax and fun in our projects we add pictures of the office to give you an idea od the mood of the business

Business

```html
<!DOCTYPE html>
<html lang="en">
<head>
<meta charset="utf-8">
<title>Tiskoro — Business Card</title>
<link rel="stylesheet" href="https://fonts.googleapis.com/css2?family=Archivo:wght@400;700&display=swap">
<style>
  :root {
    --backdrop: #d9d9d9;
    --card: #ffffff;
    --brand-yellow: #f7e11b;
    --brand-brown: #5a2a0c;
    --ink: #1c1c1c;
  }
  * { box-sizing: border-box; margin: 0; padding: 0; }
  html, body {
    width: 1200px;
    height: 800px;
    overflow: hidden;
    background: var(--backdrop);
    font-family: "Archivo", Arial, sans-serif;
  }
  .stage {
    width: 1200px;
    height: 800px;
    display: flex;
    align-items: center;
    justify-content: center;
  }
  .business-card {
    position: relative;
    width: 840px;
    height: 480px;
    background: var(--card);
    box-shadow: 0 10px 30px rgba(0,0,0,.18);
  }
  .brand {
    position: absolute;
    left: 90px;
    top: 190px;
    display: flex;
    align-items: center;
    gap: 14px;
  }
  .brand-square {
    width: 34px;
    height: 34px;
    background: var(--brand-yellow);
  }
  .brand-name {
    font-weight: 700;
    font-size: 56px;
    letter-spacing: -1.5px;
    color: var(--brand-brown);
    line-height: 1;
  }
  .divider {
    position: absolute;
    left: 398px;
    top: 110px;
    width: 3px;
    height: 230px;
    background: var(--brand-brown);
  }
  .contact {
    position: absolute;
    left: 430px;
    top: 108px;
    color: var(--ink);
  }
  .person-name {
    font-weight: 700;
    font-size: 26px;
    color: var(--brand-brown);
    line-height: 1.1;
  }
  .person-role {
    font-size: 23px;
    color: var(--brand-brown);
    margin-bottom: 14px;
  }
  .contact-list { list-style: none; }
  .contact-item {
    display: flex;
    align-items: center;
    gap: 8px;
    font-size: 25px;
    line-height: 1.35;
  }
  .contact-label {
    display: inline-flex;
    align-items: center;
    justify-content: center;
    width: 30px;
    height: 26px;
    background: var(--brand-yellow);
    color: var(--brand-brown);
    font-weight: 700;
    font-size: 19px;
  }
</style>
</head>
<body>
  <main class="stage">
    <article class="business-card">
      <div class="brand">
        <span class="brand-square"></span>
        <span class="brand-name">Tiskoro</span>
      </div>
      <div class="divider"></div>
      <section class="contact">
        <p class="person-name">Name Here</p>
        <p class="person-role">Managing Director</p>
        <ul class="contact-list">
          <li class="contact-item"><span class="contact-label">m.</span>+00 585 8888 99</li>
          <li class="contact-item"><span class="contact-label">e.</span>xxxx@xxxxxxx.com</li>
          <li class="contact-item"><span class="contact-label">w.</span>www.xxxxxxxx.com</li>
        </ul>
      </section>
    </article>
  </main>
</body>
</html>
```